birchwell hollow cattle company website

we would like a home page, an about us page, a page for sires, a page for dams, A sale page where we can list progreny for sale and a contact us. on the about us page we would like there to be a family picture. on the sires page we would like to have a picture of each sire, a description beside them and a link to their online profile at northern hereford registry. on the dam page we would like to have a picture of each dam, aswell as a description beside them aswell as a link to the northern hereford registry site. would like the website to very mobile phone friendly as expecting most traffic to be on phone. we would like the website to look and feel very mich like a farm, rustic, barbed wire and other farm feels. we would also like a frozen genetics pages where we can include pictures and descriptions of the sires and dams aswell as a price for embryos and semen. we need to website to be easy to maintain so we can update pictures and information as it changes, we would like there to be a feature so that people can sign up to be on our mailing list by giving us their mailing addess and email and full name
aswell as an area where they can send us a message to contact us.

leaving for work for 3 weeks in the canadian arctic will have limited ability to use the internet

Target Market(s)

other ranchers, farmers, cattlemen,

Industry/Entity Type

farming, agriculture, cattle

Coding

Coded - Design and coding required

Requirements
Must have
• about page, contact page, sires page, dams page, SALE page.
Nice to have
• country/farm vibe, barbed wire, wood,

```html
<!DOCTYPE html>
<html lang="en">
<head>
<meta charset="utf-8">
<title>Birchwell Hollow Cattle Company</title>
<link href="https://fonts.googleapis.com/css2?family=Anton&family=Roboto:ital,wght@0,400;0,500;0,700;1,400&display=swap" rel="stylesheet">
<style>
:root{
  --maroon:#7a2520;
  --maroon-dark:#5e1a16;
  --ink:#1e1e1e;
  --text:#555;
  --cream:#ece6dc;
  --tan:#d9c7a8;
  --white:#fff;
  --footer:#121619;
}
*{box-sizing:border-box;margin:0;padding:0}
html,body{width:1200px;height:3820px;overflow:hidden}
body{position:relative;font-family:"Roboto",sans-serif;color:var(--ink);background:var(--white)}
a{text-decoration:none}
.abs{position:absolute}
h2.section-title{font-family:"Anton",sans-serif;font-weight:400;font-size:46px;text-align:center;letter-spacing:.5px}
.title-rule{width:102px;height:3px;background:var(--maroon);margin:14px auto 0}

/* header */
.site-header{position:absolute;left:0;top:0;width:1200px;height:114px;background:#fff;border-top:4px solid #5a3a2a;z-index:5}
.brand{position:absolute;left:150px;top:20px;width:170px;text-align:center;font-weight:700;font-size:14px;line-height:18px;color:var(--ink);letter-spacing:.3px}
.brand-mark{display:block;width:30px;height:30px;border-radius:50%;background:var(--ink);margin:0 auto 8px}
.topbar{position:absolute;left:531px;top:-4px;width:524px;height:44px;background:var(--maroon-dark);border-radius:0 0 22px 22px;display:flex;align-items:center;justify-content:space-around;color:#fff;font-size:13px}
.topbar span{display:flex;align-items:center;gap:8px}
.topbar .ico{width:22px;height:22px;border-radius:50%;background:#fff;display:flex;align-items:center;justify-content:center}
.main-nav a{position:absolute;top:68px;font-size:17px;color:var(--ink)}
.main-nav a.active{color:var(--maroon)}
.main-nav a.active::after{content:"";position:absolute;left:0;right:0;bottom:-14px;height:3px;background:var(--maroon)}

/* hero */
.hero{position:absolute;left:0;top:114px;width:1200px;height:600px;background:linear-gradient(100deg,#7d8fb4 0%,#b9c4d8 35%,#8a6a55 60%,#6b4a36 75%,#a7b0c7 100%)}
.hero-title{position:absolute;left:138px;top:150px;font-family:"Anton",sans-serif;font-weight:400;font-size:66px;line-height:72px;color:#fff}
.hero-sub{position:absolute;left:142px;top:302px;font-size:22px;color:#fff}
.btn{display:inline-flex;align-items:center;justify-content:center;background:var(--maroon);color:#fff;font-weight:700;font-size:15px;border-radius:22px}
.hero .btn{position:absolute;left:142px;top:355px;width:166px;height:40px}
.contact-tab{position:absolute;right:0;top:296px;width:44px;height:162px;background:var(--maroon);border-radius:22px 0 0 22px;color:#fff;font-weight:700;font-size:13px;writing-mode:vertical-rl;display:flex;align-items:center;justify-content:center;z-index:6}

/* about */
.about-photo-ring{position:absolute;left:130px;top:763px;width:476px;height:476px;border-radius:50%;border:2px solid var(--maroon)}
.about-photo{position:absolute;left:144px;top:777px;width:448px;height:448px;border-radius:50%;background:linear-gradient(160deg,#7a6650,#4b3b2c 55%,#8e8376)}
.about-badge{position:absolute;left:376px;top:1087px;width:180px;height:180px;border-radius:50%;background:#fff;display:flex;align-items:center;justify-content:center}
.about-badge i{display:block;width:150px;height:150px;border-radius:50%;background:#2a2623;border:4px solid #c9a64a}
.about-text{position:absolute;left:629px;top:770px;width:426px}
.about-text h2{font-family:"Anton",sans-serif;font-weight:400;font-size:44px}
.about-text .rule{width:102px;height:3px;background:var(--maroon);margin:10px 0 24px}
.about-text p{font-size:15.5px;line-height:22.4px;color:var(--text);text-align:justify;margin-bottom:18px}
.about-text .btn{width:164px;height:42px;margin-top:4px;box-shadow:0 4px 8px rgba(0,0,0,.25)}
.bull-figure{position:absolute;left:968px;top:1204px;width:222px;height:118px;border-radius:50% 50% 6px 6px/60% 60% 6px 6px;background:radial-gradient(ellipse at 50% 70%,#3a3a3a 0%,#8a8a8a 60%,rgba(255,255,255,0) 72%)}

/* plain fence band */
.fence-line{position:absolute;left:0;width:1200px;height:4px;background:#151515;z-index:3}

/* sires */
.sires{position:absolute;left:0;top:1328px;width:1200px;height:640px;background:linear-gradient(180deg,#efeae2,#e5ded3)}
.sires h2.section-title{padding-top:76px}
.sire{position:absolute;top:175px;width:300px;text-align:center}
.sire-ring{position:relative;width:272px;height:246px;margin:0 auto;border-radius:58% 42% 48% 52%/48% 56% 44% 52%;border-top:4px solid var(--maroon);border-right:4px solid var(--maroon)}
.sire-img{position:absolute;left:0;top:8px;width:262px;height:236px;border-radius:58% 42% 48% 52%/48% 56% 44% 52%}
.sire h3{font-size:17px;font-weight:700;line-height:24px;margin-top:38px;color:#333}
.sire p{font-size:13px;line-height:20px;color:#777;margin-top:6px}
.arrow{position:absolute;width:48px;height:48px;border-radius:50%;background:var(--tan);display:flex;align-items:center;justify-content:center}

/* sale */
.sale{position:absolute;left:0;top:1968px;width:1200px;height:765px;background:linear-gradient(180deg,#7d241d,#8f2f24 50%,#7a231c)}
.sale h2.section-title{color:#fff;padding-top:90px}
.sale .title-rule{background:#fff}
.tile{position:absolute;border-radius:6px}
.tile.sel{border:3px solid #fff}
.tile .plus{position:absolute;left:50%;top:50%;width:52px;height:52px;margin:-26px 0 0 -26px;border-radius:50%;background:#fff;color:var(--maroon);font-size:30px;display:flex;align-items:center;justify-content:center}
.sale .btn-light{position:absolute;left:497px;top:654px;width:206px;height:38px;border-radius:19px;background:var(--cream);color:var(--maroon);font-weight:700;font-size:15px;display:flex;align-items:center;justify-content:center}

/* reviews */
.reviews{position:absolute;left:0;top:2735px;width:1200px;height:670px;background:linear-gradient(180deg,#ffffff 0%,#eef0ee 30%,#9aa69a 65%,#50603f 90%)}
.reviews h2.section-title{padding-top:74px}
.review{position:absolute;top:175px;width:432px;height:228px;background:#fff;padding:28px 30px}
.review p{font-style:italic;font-size:13px;line-height:20px;color:#666}
.reviewer{display:flex;align-items:center;gap:12px;margin-top:16px}
.avatar{width:66px;height:66px;border-radius:50%;background:#c9b9a6}
.reviewer b{display:block;font-size:19px;font-weight:500;color:#1f2f4a}
.reviewer small{font-size:12px;color:#777}
.quote{position:absolute;right:22px;bottom:-14px;font-family:"Anton",sans-serif;font-size:80px;line-height:60px;color:var(--maroon)}

/* footer */
.site-footer{position:absolute;left:0;top:3396px;width:1200px;height:424px;background:var(--footer);color:#fff}
.footer-col{position:absolute;top:118px}
.footer-col h4{font-size:24px;font-weight:500;margin-bottom:22px}
.footer-col ul{list-style:none;font-size:13.5px;line-height:24px}
.quick li::before{content:"»";margin-right:14px}
.contact-list li{display:flex;align-items:flex-start;gap:14px;margin-bottom:24px}
.contact-list svg{margin-top:6px;flex:none}
.news-input{width:311px;height:38px;background:#fff;border-radius:4px;color:#888;font-size:13.5px;padding:10px 14px}
.news-btn{width:151px;height:38px;margin-top:16px;border-radius:19px;background:var(--maroon);font-weight:700;font-size:15px;display:flex;align-items:center;justify-content:center}
.copyright{position:absolute;left:0;bottom:0;width:1200px;height:76px;background:#0c0f11;font-size:15px;display:flex;align-items:center;justify-content:center}
</style>
</head>
<body>

<header class="site-header">
  <div class="brand"><span class="brand-mark"></span>BIRCHWELL HOLLOW<br>CATTLE COMPANY</div>
  <div class="topbar">
    <span><i class="ico"><svg width="12" height="12" viewBox="0 0 24 24"><path fill="#7a2520" d="M6.6 10.8a15.1 15.1 0 0 0 6.6 6.6l2.2-2.2c.3-.3.7-.4 1-.2 1.1.4 2.3.6 3.6.6.6 0 1 .4 1 1V20c0 .6-.4 1-1 1A17 17 0 0 1 3 4c0-.6.4-1 1-1h3.5c.6 0 1 .4 1 1 0 1.3.2 2.5.6 3.6.1.3 0 .7-.2 1z"/></svg></i>Call Us : +1 888 888 8888</span>
    <span><i class="ico"><svg width="12" height="12" viewBox="0 0 24 24"><path fill="#7a2520" d="M2 5h20v14H2zm2 2v.5l8 5 8-5V7z"/></svg></i>Mail Us : info@companyname.com</span>
  </div>
  <nav class="main-nav">
    <a class="active" style="left:442px" href="#">Home</a>
    <a style="left:520px" href="#">About Us</a>
    <a style="left:623px" href="#">Sires</a>
    <a style="left:694px" href="#">Dams</a>
    <a style="left:771px" href="#">Sale</a>
    <a style="left:836px" href="#">Frozen Genetics</a>
    <a style="left:991px" href="#">Contact</a>
  </nav>
</header>

<section class="hero" role="img" aria-label="Rancher standing with a red cow and calf in a snowy pasture">
  <h1 class="hero-title">Birchwell Hollow<br>Cattle Company</h1>
  <p class="hero-sub">Raising Quality Angus Genetics with Pride</p>
  <a class="btn" href="#">GET STARTED</a>
  <div class="contact-tab">CONTACT US</div>
  <svg class="abs" style="left:0;top:500px" width="1200" height="100" viewBox="0 0 1200 100">
    <path d="M0 100 L0 90 Q600 -10 1200 90 L1200 100Z" fill="#fff"/>
    <path d="M120 82 Q600 -4 1080 82 Q600 20 120 82Z" fill="#7a2520"/>
    <circle cx="600" cy="40" r="34" fill="#fff"/>
    <path d="M600 26 V54 M590 44 L600 54 L610 44" stroke="#222" stroke-width="2.5" fill="none"/>
  </svg>
</section>

<section class="about">
  <div class="about-photo-ring"></div>
  <div class="about-photo" role="img" aria-label="Family photo in front of a rustic wooden barn door"></div>
  <div class="about-badge" role="img" aria-label="Quality badge"><i></i></div>
  <div class="about-text">
    <h2>About Us</h2>
    <div class="rule"></div>
    <p>Lorem ipsum dolor sit amet, consectetur adipiscing elit, sed do eiusmod tempor incididunt ut labore et dolore magna aliqua. Ut enim ad minim veniam, quis nostrud exercitation ullamco laboris nisi ut aliquip ex ea commodo consequat. Duis aute irure dolor in reprehenderit in voluptate velit esse cillum dolore eu fugiat nulla pariatur. Excepteur sint occaecat cupidatat non proident, sunt in culpa qui officia deserunt mollit anim id est laborum.</p>
    <p>Lorem ipsum dolor sit amet, consectetur adipiscing elit, sed do eiusmod tempor incididunt ut labore et dolore magna aliqua. Ut enim ad minim veniam, quis nostrud exercitation ullamco laboris nisi ut aliquip ex ea commodo</p>
    <a class="btn" href="#">READ MORE &nbsp;›</a>
  </div>
  <div class="bull-figure" role="img" aria-label="Silhouette of a bull standing in grass"></div>
</section>

<div class="fence-line" style="top:1324px"></div>

<section class="sires">
  <h2 class="section-title">Featured Sires</h2>
  <div class="title-rule"></div>
  <div class="arrow" style="left:40px;top:370px"><svg width="30" height="20" viewBox="0 0 30 20"><path d="M28 10H3M11 2L3 10l8 8" stroke="#111" stroke-width="2" fill="none"/></svg></div>
  <div class="arrow" style="left:1112px;top:370px"><svg width="30" height="20" viewBox="0 0 30 20"><path d="M2 10h25M19 2l8 8-8 8" stroke="#111" stroke-width="2" fill="none"/></svg></div>

  <div class="sire" style="left:126px">
    <div class="sire-ring"><div class="sire-img" role="img" aria-label="Tagged red calves on straw in winter" style="background:linear-gradient(160deg,#cfd3d6,#6d3b26 55%,#b59b72)"></div></div>
    <h3>Lorem ipsum dolor sit<br>amet, consec</h3>
    <p>Lorem ipsum dolor sit amet, consec<br>tetur adipiscing elit</p>
  </div>
  <div class="sire" style="left:449px">
    <div class="sire-ring"><div class="sire-img" role="img" aria-label="Red calf standing in a green pasture" style="background:linear-gradient(180deg,#9fb6c8,#4e6a3c 35%,#6e3326 60%,#8fa54e)"></div></div>
    <h3>Lorem ipsum dolor sit<br>amet, consec</h3>
    <p>Lorem ipsum dolor sit amet, consec<br>tetur adipiscing elit</p>
  </div>
  <div class="sire" style="left:774px">
    <div class="sire-ring"><div class="sire-img" role="img" aria-label="Red bull standing on dirt under blue sky" style="background:linear-gradient(180deg,#5d8fd0,#8a4a2a 45%,#a26a40 70%,#9c8c78)"></div></div>
    <h3>Lorem ipsum dolor sit<br>amet, consec</h3>
    <p>Lorem ipsum dolor sit amet, consec<br>tetur adipiscing elit</p>
  </div>
</section>

<section class="sale">
  <h2 class="section-title">Cattle For Sale</h2>
  <div class="title-rule"></div>
  <div class="tile" style="left:144px;top:188px;width:442px;height:209px;background:linear-gradient(180deg,#9fb0a8,#5b3424 45%,#5f8a3a)" role="img" aria-label="Red cow and calf in a green field"></div>
  <div class="tile" style="left:612px;top:188px;width:208px;height:209px;background:linear-gradient(90deg,#6e6a62,#c8b48e 50%,#8b7b62)" role="img" aria-label="Wooden livestock pen fencing"></div>
  <div class="tile" style="left:845px;top:188px;width:210px;height:209px;background:linear-gradient(180deg,#3e7ad0,#9ec0e8 45%,#6a5a45 65%,#a78e6a)" role="img" aria-label="Open cattle shelter under a blue sky"></div>
  <div class="tile" style="left:144px;top:419px;width:208px;height:210px;background:linear-gradient(120deg,#a8bad4,#eef2f7 50%,#5a5a5a)" role="img" aria-label="Fence line in fresh snow"></div>
  <div class="tile sel" style="left:375px;top:417px;width:214px;height:214px;background:linear-gradient(180deg,#3a2e2a,#6d5a52 60%,#d6d8de)" role="img" aria-label="Steel livestock gates in winter"><span class="plus">+</span></div>
  <div class="tile" style="left:613px;top:419px;width:442px;height:210px;background:linear-gradient(180deg,#c7d0cf,#8a4326 45%,#7b9a4a)" role="img" aria-label="Red cow and calf grazing"></div>
  <a class="btn-light" href="#">VIEW SALE PAGE</a>
</section>

<div class="fence-line" style="top:2731px"></div>

<section class="reviews" role="img" aria-label="Misty forest pasture with cattle walking forward">
  <h2 class="section-title">Client Reviews</h2>
  <div class="title-rule"></div>
  <div class="arrow" style="left:40px;top:264px"><svg width="30" height="20" viewBox="0 0 30 20"><path d="M28 10H3M11 2L3 10l8 8" stroke="#111" stroke-width="2" fill="none"/></svg></div>
  <div class="arrow" style="left:1112px;top:264px"><svg width="30" height="20" viewBox="0 0 30 20"><path d="M2 10h25M19 2l8 8-8 8" stroke="#111" stroke-width="2" fill="none"/></svg></div>
  <div class="review" style="left:144px">
    <p>Lorem ipsum dolor sit amet, consectetur adipiscing elit, sed do eiusmod tempor incididunt ut labore et dolore magna aliqua. Ut enim ad minim veniam, quis nostrud exercitation laboris nisi ut aliquip ex ea commodo consequat.</p>
    <div class="reviewer"><div class="avatar" role="img" aria-label="Reviewer portrait"></div><div><b>John Doe</b><small>Company name</small></div></div>
    <span class="quote">“</span>
  </div>
  <div class="review" style="left:624px">
    <p>Lorem ipsum dolor sit amet, consectetur adipiscing elit, sed do eiusmod tempor incididunt ut labore et dolore magna aliqua. Ut enim ad minim veniam, quis nostrud exercitation laboris nisi ut aliquip ex ea commodo consequat.</p>
    <div class="reviewer"><div class="avatar" role="img" aria-label="Reviewer portrait"></div><div><b>John Doe</b><small>Company name</small></div></div>
    <span class="quote">“</span>
  </div>
</section>

<footer class="site-footer">
  <svg class="abs" style="left:0;top:-20px" width="1200" height="90" viewBox="0 0 1200 90" aria-hidden="true">
    <path d="M0 20 Q600 130 1200 20 L1200 28 Q600 142 0 28Z" fill="#fff"/>
    <path d="M120 28 Q600 110 1080 28 Q600 96 120 28Z" fill="#7a2520"/>
  </svg>
  <div class="footer-col" style="left:116px">
    <h4>Quick Links</h4>
    <div style="display:flex;gap:66px">
      <ul class="quick"><li>Home</li><li>About Us</li><li>Sires</li><li>Dams</li><li>Sale</li></ul>
      <ul class="quick"><li>Frozen Genetics</li><li>Contact</li><li>Blog</li><li>FAQs</li><li>Privacy policy</li></ul>
    </div>
  </div>
  <div class="footer-col" style="left:467px">
    <h4>Contact Us</h4>
    <ul class="contact-list">
      <li><svg width="10" height="14" viewBox="0 0 10 14"><path d="M5 0a5 5 0 0 0-5 5c0 4 5 9 5 9s5-5 5-9a5 5 0 0 0-5-5zm0 7a2 2 0 1 1 0-4 2 2 0 0 1 0 4z" fill="#fff"/></svg><span>123, Lorem ipsum dolor sit<br>Southern Adelaide</span></li>
      <li><svg width="12" height="12" viewBox="0 0 24 24"><path fill="#fff" d="M6.6 10.8a15.1 15.1 0 0 0 6.6 6.6l2.2-2.2c.3-.3.7-.4 1-.2 1.1.4 2.3.6 3.6.6.6 0 1 .4 1 1V20c0 .6-.4 1-1 1A17 17 0 0 1 3 4c0-.6.4-1 1-1h3.5c.6 0 1 .4 1 1 0 1.3.2 2.5.6 3.6.1.3 0 .7-.2 1z"/></svg><span>+1 888 888 8888</span></li>
      <li><svg width="13" height="12" viewBox="0 0 24 24"><path fill="#fff" d="M2 5h20v14H2zm2 2v.5l8 5 8-5V7z"/></svg><span>info@companyname.com</span></li>
    </ul>
  </div>
  <div class="footer-col" style="left:748px">
    <h4>Subscribe to Our Newsletter</h4>
    <div class="news-input">Email address</div>
    <div class="news-btn">SUBSCRIBE</div>
  </div>
  <div class="copyright">© Copyrights 2026 | All Rights Reserved</div>
</footer>

</body>
</html>
```